Harborline Auto LLC

Car Dealer Customer Service
Address: 2874 Cresthaven Road, Shelbyville, TN 37162
web: www.harborlineautoxq.net
email: harborlineautoxq@mailnest.example
Phone: (931) 555-0148
Phone: (629) 555-0173

```html
<!DOCTYPE html>
<html lang="en">
<head>
<meta charset="utf-8">
<title>Harborline Auto – Business Card</title>
<link rel="stylesheet" href="https://fonts.googleapis.com/css2?family=Poppins:wght@500;600;700;800&display=swap">
<style>
  :root {
    --page-bg: #ffffff;
    --card-fill: #ffffff;
    --brand-blue: #1f86c4;
    --brand-blue-deep: #1a6fa3;
    --brand-gold: #ebb646;
    --ink: #1c1c1c;
  }
  html, body {
    margin: 0;
    padding: 0;
    width: 1200px;
    height: 1200px;
    overflow: hidden;
    background: var(--page-bg);
    font-family: "Poppins", sans-serif;
  }
  .sheet {
    width: 1200px;
    height: 1200px;
    display: flex;
    align-items: center;
    justify-content: center;
    gap: 50px;
  }
  .card { width: 545px; height: 324px; display: block; }
  .card-outline { fill: var(--card-fill); stroke: var(--brand-blue); stroke-width: 7; stroke-linejoin: round; }
  .brand-dot { fill: var(--brand-blue); }
  .brand-name { font-family: "Poppins", sans-serif; font-weight: 700; font-size: 36px; fill: var(--brand-blue-deep); letter-spacing: 0.5px; }
  .web-line { font-family: "Poppins", sans-serif; font-weight: 600; font-size: 19px; fill: var(--brand-gold); }
  .tagline { font-family: "Poppins", sans-serif; font-weight: 700; font-size: 35px; }
  .tag-gold { fill: var(--brand-gold); }
  .tag-blue { fill: var(--brand-blue-deep); }
  .contact { font-family: "Poppins", sans-serif; font-weight: 600; font-size: 18px; fill: var(--ink); }
  .icon { fill: none; stroke-width: 1.8; stroke-linecap: round; stroke-linejoin: round; }
  .icon-blue { stroke: var(--brand-blue); }
  .icon-gold { stroke: var(--brand-gold); }
</style>
</head>
<body>
<main class="sheet">

  <!-- Front of card -->
  <svg class="card card-front" viewBox="-6 -6 652 386" aria-label="Business card front">
    <path class="card-outline" d="M4 372 L4 190 Q4 180 16 178 L34 176 Q42 140 56 116 Q44 96 66 72 L80 50 Q92 40 112 56 L126 60 Q140 36 162 20 Q186 4 226 4 L326 4 Q346 4 356 24 L380 76 L588 76 Q596 68 598 74 L598 108 Q606 102 616 112 Q638 126 638 150 L638 372 Z"/>
    <circle class="brand-dot" cx="242" cy="130" r="62"/>
    <text class="brand-name" x="242" y="276" text-anchor="middle">HARBORLINE AUTO</text>
    <text class="web-line" x="242" y="330" text-anchor="middle">www.harborlineautoxq.net</text>
    <g transform="rotate(-90)">
      <text class="tagline tag-gold" x="-343" y="530">Car Dealer</text>
      <text class="tagline tag-gold" x="-343" y="562">Customer</text>
      <text class="tagline tag-blue" x="-343" y="594">Service</text>
    </g>
  </svg>

  <!-- Back of card -->
  <svg class="card card-back" viewBox="-6 -6 652 386" aria-label="Business card back">
    <path class="card-outline" d="M636 372 L636 190 Q636 180 624 178 L606 176 Q598 140 584 116 Q596 96 574 72 L560 50 Q548 40 528 56 L514 60 Q500 36 478 20 Q454 4 414 4 L314 4 Q294 4 284 24 L260 76 L52 76 Q44 68 42 74 L42 108 Q34 102 24 112 Q2 126 2 150 L2 372 Z"/>
    <rect x="290" y="30" width="200" height="60" rx="10" fill="url(#dealGradient)" role="img" aria-label="Illustration of a car with a handshake"/>
    <defs>
      <linearGradient id="dealGradient" x1="0" x2="1">
        <stop offset="0" stop-color="#ebb646"/>
        <stop offset="1" stop-color="#1f86c4"/>
      </linearGradient>
    </defs>
    <text class="tagline tag-gold" x="500" y="138" text-anchor="end">Car Dealer</text>
    <text class="tagline" x="500" y="178" text-anchor="end"><tspan class="tag-gold">Customer </tspan><tspan class="tag-blue">Service</tspan></text>

    <g class="contact-list">
      <path class="icon icon-blue" d="M80 218 L89 210 L98 218 M82 216 L82 228 L96 228 L96 216"/>
      <text class="contact" x="110" y="227">2874 Cresthaven Road, Shelbyville, TN 37162</text>

      <path class="icon icon-gold" d="M82 245 L96 252 L89 254 L92 262 L89 263 L86 256 L81 260 Z"/>
      <text class="contact" x="110" y="261">www.harborlineautoxq.net</text>

      <rect class="icon icon-blue" x="80" y="282" width="18" height="13" rx="2"/>
      <path class="icon icon-blue" d="M80 284 L89 291 L98 284"/>
      <text class="contact" x="110" y="295">harborlineautoxq@mailnest.example</text>

      <circle class="icon icon-gold" cx="89" cy="316" r="4.5"/>
      <path class="icon icon-gold" d="M81 331 Q81 322 89 322 Q97 322 97 331 Z"/>
      <text class="contact" x="110" y="329">(931) 555-0148 | (629) 555-0173</text>
    </g>
  </svg>

</main>
</body>
</html>
```